TA BRAMLEY BUSINESS CARD DESIGN PROJECT

We need to utilize our logo that was expertly created on PixelHarbor and now need to match this with a business card design.

```html
<!DOCTYPE html>
<html lang="en">
<head>
<meta charset="utf-8">
<title>TA Bramley Business Card</title>
<link href="https://fonts.googleapis.com/css2?family=Open+Sans:wght@400;700&display=swap" rel="stylesheet">
<style>
  :root {
    --backdrop: #3a3a3a;
    --card: #161616;
    --edge: #1f5fc4;
    --brand-blue: #1b5cbf;
    --text-light: #e8e8e8;
  }
  * { margin: 0; padding: 0; box-sizing: border-box; }
  html, body {
    width: 1200px; height: 801px; overflow: hidden;
    background: var(--backdrop);
    font-family: "Open Sans", Arial, sans-serif;
  }
  .stage {
    width: 1200px; height: 801px;
    display: flex; align-items: center; justify-content: center; gap: 40px;
  }
  .card {
    width: 540px; height: 309px;
    background: var(--card);
    border-bottom: 3px solid var(--edge);
    border-right: 3px solid var(--edge);
    position: relative;
  }
  .card-front { display: flex; }
  .brand-panel {
    width: 52%;
    display: flex; align-items: center; justify-content: center; gap: 10px;
  }
  .brand-square { width: 18px; height: 18px; background: var(--brand-blue); }
  .brand-name {
    color: var(--brand-blue); font-weight: 700; font-size: 30px; letter-spacing: 1px;
  }
  .contact-panel {
    flex: 1;
    border-left: 1px solid var(--edge);
    margin: 70px 0 60px;
    padding: 0 0 0 26px;
    display: flex; flex-direction: column; justify-content: center;
    color: var(--text-light); font-size: 13px; line-height: 1.45;
  }
  .person-name { color: var(--brand-blue); font-weight: 700; font-size: 17px; letter-spacing: .5px; }
  .person-role { margin-bottom: 12px; }
  .address { margin-bottom: 12px; }
  .contact-line { display: flex; align-items: center; gap: 7px; }
  .contact-line svg { width: 10px; height: 10px; fill: var(--brand-blue); flex: none; }
  .card-back { display: flex; align-items: center; justify-content: center; }
  .back-brand { color: #8a8a8a; font-weight: 700; font-size: 34px; letter-spacing: 1px; }
</style>
</head>
<body>
<main class="stage">
  <section class="card card-front">
    <div class="brand-panel">
      <span class="brand-square"></span>
      <span class="brand-name">TA BRAMLEY</span>
    </div>
    <div class="contact-panel">
      <p class="person-name">DORIAN VASQUEZ</p>
      <p class="person-role">President</p>
      <p class="address">1870 Marlow Cove Drive<br>Seacliff CA 93400</p>
      <p class="contact-line">
        <svg viewBox="0 0 10 10"><path d="M2 0h2l1 3-1.5 1a6 6 0 0 0 2.5 2.5L7 5l3 1v2a2 2 0 0 1-2 2A8 8 0 0 1 0 2a2 2 0 0 1 2-2z"/></svg>
        555-014-2290
      </p>
      <p class="contact-line">
        <svg viewBox="0 0 10 10"><path d="M0 2h10v6H0z"/></svg>
        d.vasquez@tabramley.com
      </p>
      <p class="contact-line">
        <svg viewBox="0 0 10 10"><circle cx="5" cy="5" r="5"/></svg>
        www.tabramley.com
      </p>
    </div>
  </section>
  <section class="card card-back">
    <span class="back-brand">TA BRAMLEY</span>
  </section>
</main>
</body>
</html>
```